Keystone Trench Co Business Card*

Looking for a professional, clean and crisp business card

I am in the underground utilities industry and am just looking for a really impressive business card. I would like our card to be white with our symbol crisp and clear with it protruding. I also have a business partner that will require his name and info on the card once the design is set. I would like to have our website info on the card which is;
http://keystonetrenchco.example/

Contact Information for Business Card

Website, contact name, number and email

```html
<!DOCTYPE html>
<html lang="en">
<head>
<meta charset="utf-8">
<title>Keystone Trench Co Business Card</title>
<link rel="stylesheet" href="https://fonts.googleapis.com/css2?family=Oswald:wght@600&family=Roboto:wght@400&display=swap">
<style>
  :root {
    --backdrop: #141414;
    --card: #222222;
    --edge: #e0242c;
    --ink: #ffffff;
    --ink-soft: #d9d9d9;
    --accent: #3a62b8;
    --emboss: #2e2e2e;
    --emboss-line: #3a3a3a;
  }
  * { margin: 0; padding: 0; box-sizing: border-box; }
  html, body {
    width: 1200px; height: 900px; overflow: hidden;
    background: var(--backdrop);
  }
  .stage {
    position: relative; width: 1200px; height: 900px;
    display: flex; flex-direction: column; align-items: center; justify-content: center; gap: 50px;
  }
  .card {
    position: relative; width: 700px; height: 400px;
    background: var(--card);
    border-bottom: 4px solid var(--edge);
    box-shadow: 0 0 0 1px var(--edge) inset;
    overflow: hidden;
  }
  .card--front { display: flex; align-items: center; justify-content: center; }
  .brand-mark { display: flex; flex-direction: column; align-items: center; gap: 18px; }
  .brand-mark__dot {
    width: 56px; height: 56px; border-radius: 50%;
    background: var(--accent);
  }
  .brand-mark__name {
    font-family: "Oswald", sans-serif; font-weight: 600;
    font-size: 44px; letter-spacing: 3px; text-transform: uppercase;
    color: var(--ink);
  }
  .emboss {
    position: absolute; right: -60px; top: -40px;
    width: 440px; height: 440px; border-radius: 50%;
    background: var(--emboss);
    box-shadow: inset 3px 3px 6px rgba(255,255,255,0.06), inset -4px -4px 8px rgba(0,0,0,0.5);
    display: flex; align-items: center; justify-content: center;
  }
  .emboss__name {
    font-family: "Oswald", sans-serif; font-weight: 600;
    font-size: 40px; letter-spacing: 3px; text-transform: uppercase;
    color: var(--emboss-line); text-align: center; line-height: 1.2;
  }
  .contact { position: absolute; left: 48px; bottom: 44px; }
  .contact__name {
    font-family: "Oswald", sans-serif; font-weight: 600;
    font-size: 34px; letter-spacing: 1px; text-transform: uppercase;
    color: var(--ink); margin-bottom: 16px;
  }
  .contact__list { list-style: none; }
  .contact__item {
    display: flex; align-items: center; gap: 12px;
    font-family: "Roboto", sans-serif; font-size: 17px; color: var(--ink-soft);
    margin-top: 6px;
  }
  .contact__icon { width: 18px; height: 18px; flex: none; }
  .contact__web-domain { color: var(--accent); }
</style>
</head>
<body>
<main class="stage">
  <section class="card card--front" aria-label="Card front">
    <div class="brand-mark">
      <span class="brand-mark__dot"></span>
      <span class="brand-mark__name">Keystone Trench Co</span>
    </div>
  </section>

  <section class="card card--back" aria-label="Card back">
    <div class="emboss">
      <span class="emboss__name">Keystone<br>Trench Co</span>
    </div>
    <div class="contact">
      <h1 class="contact__name">Dale Ostrander</h1>
      <ul class="contact__list">
        <li class="contact__item">
          <svg class="contact__icon" viewBox="0 0 24 24" fill="none" stroke="#3a62b8" stroke-width="2"><circle cx="12" cy="12" r="10"/><path d="M8.5 7.5l2 2-1 1.5c.8 1.6 1.9 2.7 3.5 3.5l1.5-1 2 2-1.5 1.5c-3.5-.5-7-4-7.5-7.5z" fill="#3a62b8" stroke="none"/></svg>
          555-014-2286
        </li>
        <li class="contact__item">
          <svg class="contact__icon" viewBox="0 0 24 24" fill="none" stroke="#3a62b8" stroke-width="2"><rect x="2" y="5" width="20" height="14" rx="1"/><path d="M2 6l10 7 10-7"/></svg>
          dale@keystonetrenchco.example
        </li>
        <li class="contact__item">
          <svg class="contact__icon" viewBox="0 0 24 24" fill="none" stroke="#3a62b8" stroke-width="2"><circle cx="12" cy="12" r="10"/><path d="M2 12h20M12 2c3 3 3 17 0 20M12 2c-3 3-3 17 0 20"/></svg>
          <span>www.<span class="contact__web-domain">keystonetrenchco</span>.example</span>
        </li>
      </ul>
    </div>
  </section>
</main>
</body>
</html>
```